Wine Bottle Label for Tall Fern Wines

We are a small, newly established winery in need of an original, bold and outstanding bottle label design for our Tall Fern wine.

Our vineyard and winery are located on a 200 acre farm in a remote part of southern Oregon. The name "Tall Fern" was inspired by the large, overgrown size of all of the foliage here, including our grapevines. Things grow large and vigorous in Oregon! And everything is very lush and green. It is almost surreal or other-worldly, like the landscapes seen in the Keeper of The Stones movies, or the land of Quill. It is a place that makes you say "wow" with its epic, large scale, natural beauty.

The name "Tall Fern" also captures the essence of our wine. It is big in flavor, quality and color. Our first release is a Pinot Noir (red). Pinot Noir wines often are subtle in flavor and thin in their color. Our label should convey that our Pinot Noir is a much more robust, darker, heavier, meatier, more flavorful wine that is a lot more fun than an "ordinary" wine. At the same time, this wine is not cheap, and so nothing in the label should convey "bargain," "low price," or "cheapness." This is a fine wine with a sense of adventure. Be sure to convey "quality" with your design along with "big," "adventure" and "fun".

The label should appeal to a younger demographic, both male and female, between the ages of 21 and 35. It should be non-traditional and adventurous and suggest a pushing of boundaries and a breaking of rules. This Pinot Noir does not conform to the normal "limitations" of the variety, therefore the label should not conform. It should have an "organic" or "natural" or "agricultural" vibe, as opposed to something mechanical or technical. It should, however, be contemporary. Do not confuse "natural" or "organic" with being nostalgic or old school. Think "agri-hipsters."

The label should be designed to fit on a Burgundy-style wine bottle (photo attached for reference). (Note: All Pinot Noir and Chardonnay is bottled in Burgundy bottles, If you are not sure about the bottle shape you can go to a local store and compare the various bottles. Locate a bottle of Pinot Noir or Chardonnay or anything identified as a "Burgundy Wine," and it should be the correct bottle. The tall, skinny bottles used for Cabernet Sauvignon are NOT correct)). Please see the "Must Have" notes for more on the bottle.

In summary, the final project should be a wine bottle label design that conveys bigness, vastness, adventurous, non-traditional, high quality wine. A good tagline to keep in mind is "Living Large."

Target Market(s)

Young, hip, non-conformist wine drinkers aged 21-35 with a sense of adventure and an appreciation of quality.

Industry/Entity Type

School

Requirements
Must have
• *Must contain the words:

Tall Fern (the brand)
2013 Pinot Noir (the vintage year and variety)

*The label must be designed to fit a Burgundy-style wine bottle. A photo is attached for reference.

*Additionally, the label needs to fit on the lower, widest part of the bottle. The label will be printed on sticky paper and rolled onto the bottle with a machine. The machine cannot apply labels to the neck of the bottle. The maximum size of a label that will fit this space is 5.5 inches wide by 4.5 inches tall. You DO NOT have to fill ALL of this space or confine the label shape to a rectangle, but the label cannot exceed this size or it won't stick to the bottle properly. It will really help if you can put your hands on an actual bottle to see the logistics of applying the label. But if that is not possible, just do your best with the instructions you have. I am confident the winning design could be adjusted to fit the bottle, if necessary
Nice to have
• *Wine grape leaf or leaves.

*A concept I have been playing with is sunlight shining through leaves like light through a Marlowe lamp or a stained glass window. This is NOT a requirement for this label. However, if the concept inspires and idea, I would be most happy to see it.
Should not have
• IF a leaf or leaves are included in the design (not a requirement) they MUST be wine grapevine leafs and preferably leaves of the Pinot Noir vine. Do not use generic leaves or identifiable leaves such as oak leaves, maple leaves, or anything that looks like the Canadian flag or the Halden Ridge Ravens hockey logo. Reference the attached photos of wine grape leaves to see the correct leaf type. I am happy to email more photos upon request. These photos may be used in whole or in part in your design, however, a leaf from a photo is NOT a requirement, nor is the image of a leaf or leaves.

This label should NOT be designed for Bordeaux-style wine bottles (the tall, skinny ones).

```html
<!DOCTYPE html>
<html lang="en">
<head>
<meta charset="utf-8">
<title>Tall Fern Wines — 2013 Pinot Noir Label</title>
<link rel="stylesheet" href="https://fonts.googleapis.com/css2?family=Alex+Brush&family=MedievalSharp&family=Tinos&display=swap">
<style>
  :root {
    --label-red: #b5261e;
    --parchment: #f0c66e;
    --leaf-deep: #2f8a3a;
    --leaf-mid: #5aa532;
    --leaf-light: #9bc22e;
    --ink: #111111;
    --wine: #b0221c;
    --badge-yellow: #e6dc4a;
  }
  * { margin: 0; padding: 0; box-sizing: border-box; }
  html, body {
    width: 1200px;
    height: 624px;
    overflow: hidden;
    background: var(--label-red);
  }
  .label {
    position: relative;
    width: 1200px;
    height: 624px;
    background: var(--label-red);
  }
  .label__panel {
    position: absolute;
    left: 23px;
    top: 23px;
    width: 1153px;
    height: 577px;
    background: var(--parchment);
  }
  .label__foliage {
    position: absolute;
    inset: 0;
    width: 1200px;
    height: 624px;
  }
  .label__vintage {
    position: absolute;
    left: 531px;
    top: 55px;
    width: 138px;
    height: 138px;
  }
  .label__vintage-year {
    position: absolute;
    left: 531px;
    top: 104px;
    width: 138px;
    text-align: center;
    font-family: "Tinos", serif;
    font-size: 32px;
    line-height: 40px;
    color: var(--ink);
  }
  .label__brand {
    position: absolute;
    left: 0;
    width: 1200px;
    top: 165px;
    text-align: center;
    font-family: "Alex Brush", cursive;
    font-weight: 400;
    font-size: 215px;
    line-height: 260px;
    color: var(--wine);
    text-shadow:
      1.5px 0 0 var(--ink), -1.5px 0 0 var(--ink),
      0 1.5px 0 var(--ink), 0 -1.5px 0 var(--ink),
      1px 1px 0 var(--ink), -1px -1px 0 var(--ink),
      1px -1px 0 var(--ink), -1px 1px 0 var(--ink),
      4px 4px 5px rgba(0, 0, 0, 0.45);
    white-space: nowrap;
  }
  .label__variety {
    position: absolute;
    left: 398px;
    width: 400px;
    top: 490px;
    text-align: center;
    font-family: "MedievalSharp", serif;
    font-size: 42px;
    line-height: 50px;
    color: var(--ink);
    text-shadow: 2px 2px 3px rgba(0, 0, 0, 0.35);
    white-space: nowrap;
  }
  .label__volume,
  .label__abv {
    position: absolute;
    top: 536px;
    font-family: "Tinos", serif;
    font-size: 27px;
    line-height: 34px;
    color: var(--ink);
  }
  .label__volume { left: 71px; }
  .label__abv { right: 59px; }
</style>
</head>
<body>
  <main class="label">
    <div class="label__panel"></div>

    <svg class="label__foliage" viewBox="0 0 1476 768" preserveAspectRatio="none"
         role="img" aria-label="Close-up illustration of large green grapevine leaves with dark veins">
      <defs>
        <linearGradient id="foliage-tone" x1="0" y1="0" x2="1" y2="0.6">
          <stop offset="0" stop-color="var(--leaf-deep)"/>
          <stop offset="0.45" stop-color="var(--leaf-mid)"/>
          <stop offset="1" stop-color="var(--leaf-light)"/>
        </linearGradient>
      </defs>
      <polygon fill="url(#foliage-tone)"
        points="0,0 1400,0 1390,90 1300,165 1190,225 1080,262 960,300 820,330 700,330 620,360 570,440 530,540 490,585 440,620 400,655 330,635 230,605 130,580 40,565 0,560"/>
    </svg>

    <svg class="label__vintage" viewBox="0 0 138 138" role="img" aria-label="Round vintage medallion with a swirling ornamental border">
      <circle cx="69" cy="69" r="69" fill="var(--ink)"/>
      <circle cx="69" cy="69" r="52" fill="var(--badge-yellow)"/>
    </svg>
    <div class="label__vintage-year">2013</div>

    <h1 class="label__brand">Tall Fern</h1>
    <p class="label__variety">Pinot Noir</p>
    <p class="label__volume">750 ml</p>
    <p class="label__abv">..%Alc./Vol</p>
  </main>
</body>
</html>
```